VELTAR WEBSITE

need to create a new website for VELTAR ltd
the company deals with all aspects of safety products & safety wear
we need a simple website to show
ideas can be taken from following website whose products we shall distribute in kenya
www.kwr.co.uk
www.dorvik.eu
www.brimtoolsupplyco.com
www.gardvalewerks.co.za

we need following tabs
1) home - basic company information
2) products - broken down to following categories ie gloves, head protection, ear protection, mouth protection, foot protection
3) contacts

the company profile is a reputable company dealing with all aspects of safety, HSE (health and safety equipment), and PPE (personal protective equipment)

the website should have the dorvik logo for which we are an authorized distributor.
the dorvi industrial range writeup can be picked from their website
Updates

Dear Designers, i shall be able to choose a final design in 2 weeks, sorry i have not been able to finalise this due to a personal reason

Target Market(s)

the buyers are all types of industry who care for their employees safety

Industry/Entity Type

Industrial

Requirements
Must have
• clean look, fresh look, user freindly
Nice to have
• clear images, quick links etc

```html
<!DOCTYPE html>
<html lang="en">
<head>
<meta charset="utf-8">
<title>VELTAR – Specialized Protective &amp; Industrial Products</title>
<link href="https://fonts.googleapis.com/css2?family=Open+Sans:wght@300;400;600&display=swap" rel="stylesheet">
<style>
  :root{
    --navy:#0d2d3c;
    --yellow:#f5b21a;
    --text:#333;
    --muted:#9a9a9a;
    --bar:#e3e3e3;
    --line:#ececec;
    --footer:#232323;
    --sky:#dff1f7;
  }
  *{margin:0;padding:0;box-sizing:border-box}
  html,body{width:1029px;height:1200px;overflow:hidden}
  body{
    position:relative;
    font-family:'Open Sans',sans-serif;
    color:var(--text);
    background:
      radial-gradient(ellipse 700px 260px at 520px 40px,#ffffff 0%,rgba(255,255,255,0) 70%),
      linear-gradient(180deg,var(--sky) 0px,#eef8fb 180px,#ffffff 330px,#ffffff 100%);
  }
  .top-rule{position:absolute;left:0;top:0;width:100%;height:4px;background:var(--navy)}

  .brand{position:absolute;left:97px;top:62px;display:flex;align-items:center;gap:8px}
  .brand-mark{width:22px;height:22px;background:var(--yellow)}
  .brand-name{font-size:30px;font-weight:600;color:var(--navy);letter-spacing:1px}

  .main-nav{position:absolute;top:54px;left:623px}
  .nav-item{position:absolute;top:0;white-space:nowrap}
  .nav-num{display:block;font-size:12px;font-weight:400;color:var(--yellow);margin-left:2px}
  .nav-item.is-active .nav-num{color:var(--navy)}
  .nav-label{display:inline-block;margin-top:3px;font-size:13.5px;color:var(--navy);padding-bottom:1px;border-bottom:3px solid #9c9c9c}
  .nav-item.is-active .nav-label{border-bottom-color:var(--navy)}
  .caret{display:inline-block;margin-left:5px;vertical-align:middle;border:3.5px solid transparent;border-top:4px solid var(--navy);transform:translateY(2px)}

  .tool-btn{position:absolute;top:65px;width:32px;height:32px;border-radius:50%;display:flex;align-items:center;justify-content:center}
  .tool-share{left:867px;background:var(--navy)}
  .tool-search{left:903px;background:#d2d2cc}

  .hero{position:absolute;left:97px;top:141px;width:839px;height:391px;overflow:hidden;
    background:linear-gradient(90deg,#f3f2ee 0%,#e8e7e3 40%,#ddd9cf 55%,#c9c1a8 68%,#a7aab0 82%,#6f88a2 100%)}
  .hero-title{position:absolute;left:32px;top:122px;font-size:28.5px;font-weight:300;line-height:34px;color:var(--navy);letter-spacing:-.3px}
  .hero-title strong{font-weight:400}
  .hero-cta{position:absolute;left:25px;top:207px;width:226px;height:35px;border-radius:18px;background:#cfcfcf;
    display:flex;align-items:center;padding-left:13px;font-size:12.5px;color:var(--navy)}
  .hero-cta svg{position:absolute;right:11px;top:8px}
  .hero-dots{position:absolute;left:39px;top:252px;display:flex;gap:3px}
  .hero-dots span{width:5px;height:5px;border-radius:50%;background:var(--navy)}
  .hero-dots span:first-child{background:var(--yellow)}
  .hero-shadow{position:absolute;left:120px;top:530px;width:790px;height:18px;
    background:radial-gradient(ellipse at 50% 0%,rgba(0,0,0,.45) 0%,rgba(0,0,0,0) 70%)}

  .section-bar{position:absolute;left:97px;top:573px;width:840px;height:38px;background:var(--bar)}
  .section-bar h2{position:absolute;left:9px;top:8px;font-size:19px;font-weight:600;color:var(--navy);letter-spacing:-.3px}
  .section-bar svg{position:absolute;right:19px;top:13px}

  .service{position:absolute;top:654px;width:219px}
  .service h3{font-size:16px;font-weight:400;color:var(--navy);height:25px;border-bottom:3px solid var(--line);position:relative}
  .service h3::after{content:"";position:absolute;left:0;bottom:-3px;width:23px;height:3px;background:var(--yellow)}
  .service-photo{margin-top:13px;width:219px;height:81px}
  .service p{margin:11px 0 0 3px;width:220px;font-size:9.6px;line-height:12.3px;color:var(--text);letter-spacing:-.1px}
  .read-more{display:flex;align-items:center;gap:6px;margin:20px 0 0 5px;font-size:11px;color:var(--text)}
  .read-more i{width:13px;height:13px;border-radius:50%;background:var(--yellow);position:relative}
  .read-more i::after{content:"";position:absolute;left:4px;top:4px;width:3px;height:3px;border-top:1.3px solid #fff;border-right:1.3px solid #fff;transform:rotate(45deg)}

  .block-title{position:absolute;font-size:17px;font-weight:400;color:var(--navy);height:26px;border-bottom:3px solid var(--line)}
  .block-title::after{content:"";position:absolute;left:0;bottom:-3px;width:96px;height:3px;background:var(--navy)}
  .about-title{left:107px;top:940px;width:534px}
  .testi-title{left:695px;top:938px;width:242px}
  .testi-title::after{width:56px}

  .about-photo{position:absolute;left:107px;top:982px;width:202px;height:134px;
    background:linear-gradient(135deg,#7d6a4c 0%,#56708c 45%,#47688c 70%,#a58a4a 100%)}
  .about-text{position:absolute;left:320px;top:983px;width:320px;font-size:10.4px;line-height:17.1px;color:var(--muted);letter-spacing:-.1px}

  .testimonial{position:absolute;left:695px;top:980px;width:242px}
  .quote-mark{position:absolute;font-size:30px;font-weight:600;font-style:italic;color:var(--navy);line-height:1}
  .quote-open{left:2px;top:-4px}
  .quote-close{right:3px;top:77px}
  .testimonial p{margin-left:21px;font-size:10.7px;line-height:14.6px;color:var(--text)}
  .testimonial cite{display:block;text-align:right;margin:9px 19px 0 0;font-style:normal;font-size:11px;color:var(--navy)}

  .site-footer{position:absolute;left:0;top:1155px;width:100%;height:45px;background:var(--footer);
    display:flex;align-items:center;justify-content:center;font-size:10px;color:#fff}
</style>
</head>
<body>
  <div class="top-rule"></div>

  <header>
    <div class="brand"><span class="brand-mark"></span><span class="brand-name">VELTAR</span></div>
    <nav class="main-nav">
      <a class="nav-item is-active" style="left:0"><span class="nav-num">01</span><span class="nav-label">Home</span></a>
      <a class="nav-item" style="left:66px"><span class="nav-num">02</span><span class="nav-label">Products<span class="caret"></span></span></a>
      <a class="nav-item" style="left:148px"><span class="nav-num">03</span><span class="nav-label">Contact Us</span></a>
    </nav>
    <span class="tool-btn tool-share">
      <svg width="14" height="14" viewBox="0 0 14 14"><g fill="#fff"><circle cx="3" cy="7" r="2"/><circle cx="11" cy="3" r="2"/><circle cx="11" cy="11" r="2"/></g><path d="M3 7L11 3M3 7L11 11" stroke="#fff" stroke-width="1.3"/></svg>
    </span>
    <span class="tool-btn tool-search">
      <svg width="14" height="14" viewBox="0 0 14 14"><circle cx="6" cy="6" r="4" fill="none" stroke="#fff" stroke-width="2"/><path d="M9 9l3.5 3.5" stroke="#fff" stroke-width="2.2" stroke-linecap="round"/></svg>
    </span>
  </header>

  <section class="hero" role="img" aria-label="Gloved hand holding a yellow hard hat next to a worker's tool belt">
    <h1 class="hero-title"><strong>VELTAR</strong> Specialized Protective<br>&amp; Industrial Products</h1>
    <a class="hero-cta">Learn more about the VELTAR
      <svg width="18" height="18" viewBox="0 0 18 18"><circle cx="9" cy="9" r="9" fill="var(--navy)"/><path d="M4.5 9h7M8.5 5.5L12 9l-3.5 3.5" stroke="#fff" stroke-width="2" fill="none"/></svg>
    </a>
    <div class="hero-dots"><span></span><span></span><span></span><span></span></div>
  </section>
  <div class="hero-shadow"></div>

  <div class="section-bar">
    <h2>OUR SERVICES</h2>
    <svg width="20" height="11" viewBox="0 0 20 11"><path d="M7 0v11L0 5.5z M13 0v11l7-5.5z" fill="var(--navy)"/></svg>
  </div>

  <article class="service" style="left:106px">
    <h3>Gloves</h3>
    <div class="service-photo" role="img" aria-label="Hands pulling on blue nitrile gloves" style="background:linear-gradient(90deg,#b9c6dc,#6f9fd8 40%,#5a8fd2 70%,#d9c4b6)"></div>
    <p>Lorem Ipsum is simply dummy text of the printing and typesetting industry. Lorem Lorem Ipsum is simply dummy text of the printing and typesetting industry. Lorem</p>
    <a class="read-more"><i></i>Read More</a>
  </article>
  <article class="service" style="left:400px">
    <h3>Head Protection</h3>
    <div class="service-photo" role="img" aria-label="Worker in a blue hard hat and safety glasses" style="background:linear-gradient(90deg,#6f7378,#51708f 45%,#8c8f93 80%,#b6b8ba)"></div>
    <p>Lorem Ipsum is simply dummy text of the printing and typesetting industry. Lorem Lorem Ipsum is simply dummy text of the printing and typesetting industry. Lorem</p>
    <a class="read-more"><i></i>Read More</a>
  </article>
  <article class="service" style="left:692px">
    <h3>Foot Protection</h3>
    <div class="service-photo" role="img" aria-label="Two clear mouth guards on a wooden surface" style="background:linear-gradient(90deg,#9a5a2a,#b98a5c 50%,#94592c)"></div>
    <p>Lorem Ipsum is simply dummy text of the printing and typesetting industry. Lorem Lorem Ipsum is simply dummy text of the printing and typesetting industry. Lorem</p>
    <a class="read-more"><i></i>Read More</a>
  </article>

  <h2 class="block-title about-title">About Us</h2>
  <div class="about-photo" role="img" aria-label="Worker in face shield and hard hat using an angle grinder"></div>
  <p class="about-text">Lorem Ipsum is simply dummy text of the printing and typesetting industry. Lorem Lorem Ipsum is simply dummy text of the printing and typesetting industry. Lorem Lorem Ipsum is simply dummy text of the printing and typesetting industry. Lorem Lorem Ipsum is simply dummy text of the printing and typesetting industry. Lorem Lorem Ipsum is simply dummy text of the printing and typesetting industry. Lorem Lorem Ipsum is simply dummy text of the printing and typesetting industry.</p>

  <h2 class="block-title testi-title">Our Testimonials</h2>
  <blockquote class="testimonial">
    <span class="quote-mark quote-open">"</span>
    <p>Lorem Ipsum is simply dummy text of the printing and typesetting industry. Lorem Lorem Ipsum is simply dummy text of the printing and typesetting industry. Lorem Lorem Ipsum is simply dummy text of the</p>
    <span class="quote-mark quote-close">"</span>
    <cite>Marten Olsby</cite>
  </blockquote>

  <footer class="site-footer">Copyright © 2013 VELTAR. All rights reserved.</footer>
</body>
</html>
```